New Business Card Design for Manufacturing

We are an engineering/manufacturing company that offers Advanced machining/assembly/engineering services, as well as innovative products for the heavy duty engine cooling markets.

We are looking to get a new business card designed that is clean and modern looking, but still fits the wide range of technical/skilled work we do.

- We hope to use this design as the base for other design work in new Presentations, web, and print work.

Industry/Entity Type

Engineering

Contact Information for Business Card

Our preferred color of blue is (RGB) 22/71/159 but can vary slightly from that color. Our content will be our Logo and full company name (Vantrell Forge Works, Inc.), company address, name, job title, phone number with extension, cell number, fax number, website, and email address on the cards.
We'd like the full company name next to the logo, but we are open to other interpretations of that layout.
Preferably, we would like the back side to be clean with just our logo, and the front to contain all of the contact information.

Colors
2f74b4
0355a3
85abd2

Requirements
Must have
• - Logo, company name, needed content - We are open to interpretation beyond that.
• - Standard size business card.
• - Horizontal orientation.
• - Enough space for lengthy names / job titles (for example, a job title could read "Directory of Human Resources" or "V.P. of Governmental Affairs"). We need this to look clean, whether the title be short (CEO) or long (as described above).

```html
<!DOCTYPE html>
<html lang="en">
<head>
<meta charset="utf-8">
<title>Vantrell Forge Works — Business Card</title>
<link rel="stylesheet" href="https://fonts.googleapis.com/css2?family=Roboto:wght@400;500;700;900&display=swap">
<style>
  :root {
    --backdrop: #e9e7e4;
    --card-back: #121212;
    --card-front: #1b1b1c;
    --brand-blue: #2f74d4;
    --mark-grey: #3a3a3c;
    --text-white: #f2f2f2;
    --text-grey: #8d8d90;
  }
  * { box-sizing: border-box; margin: 0; padding: 0; }
  html, body { width: 1200px; height: 716px; overflow: hidden; }
  body {
    background: var(--backdrop);
    font-family: "Roboto", Arial, sans-serif;
    display: flex;
    align-items: center;
    justify-content: center;
    gap: 44px;
  }
  .card {
    position: relative;
    width: 520px;
    height: 297px;
    border-radius: 3px;
    box-shadow: 0 10px 28px rgba(0,0,0,0.22);
  }
  .card--back { background: var(--card-back); }
  .card--front { background: var(--card-front); }

  /* back side */
  .back-lockup {
    position: absolute;
    left: 40px;
    top: 106px;
    display: flex;
    align-items: center;
    gap: 22px;
  }
  .wordmark {
    font-weight: 900;
    text-transform: uppercase;
    line-height: 1;
  }
  .wordmark__name { font-size: 40px; letter-spacing: 1px; }
  .wordmark__tagline {
    font-size: 10px;
    font-weight: 700;
    letter-spacing: 1.2px;
    margin-top: 6px;
  }
  .card--back .wordmark { color: var(--mark-grey); }
  .company-name {
    color: var(--text-white);
    font-weight: 700;
    font-size: 15px;
    line-height: 1.05;
    text-transform: uppercase;
    letter-spacing: 0.5px;
  }
  .company-name small { font-size: 8px; margin-left: 2px; }

  /* front side */
  .card--front .wordmark {
    position: absolute;
    left: 30px;
    top: 30px;
    color: var(--brand-blue);
  }
  .address {
    position: absolute;
    left: 30px;
    top: 196px;
    color: var(--text-grey);
    font-size: 12px;
    line-height: 1.45;
  }
  .person {
    position: absolute;
    left: 300px;
    top: 150px;
  }
  .person__name {
    color: var(--brand-blue);
    font-size: 19px;
    font-weight: 500;
  }
  .person__title {
    color: var(--text-white);
    font-size: 13px;
    margin-top: 2px;
  }
  .contact-list {
    list-style: none;
    margin-top: 10px;
  }
  .contact-list li {
    display: flex;
    align-items: center;
    gap: 7px;
    color: var(--text-white);
    font-size: 12px;
    line-height: 18px;
  }
  .contact-list svg { width: 11px; height: 11px; fill: var(--brand-blue); flex: none; }
</style>
</head>
<body>

  <section class="card card--back" aria-label="Card back">
    <div class="back-lockup">
      <div class="wordmark">
        <div class="wordmark__name">Vantrell</div>
        <div class="wordmark__tagline">Built to Endure</div>
      </div>
      <div class="company-name">Vantrell<br>Forge<br>Works<small>INC</small></div>
    </div>
  </section>

  <section class="card card--front" aria-label="Card front">
    <div class="wordmark">
      <div class="wordmark__name">Vantrell</div>
      <div class="wordmark__tagline">Built to Endure</div>
    </div>

    <address class="address" style="font-style:normal">
      Level 2, 17 Carden Lane<br>Ashford, VIC 3150
    </address>

    <div class="person">
      <div class="person__name">Daniel Harker</div>
      <div class="person__title">V.P. of Governmental Affairs</div>
      <ul class="contact-list">
        <li><svg viewBox="0 0 24 24" aria-hidden="true"><path d="M6.6 10.8a15 15 0 0 0 6.6 6.6l2.2-2.2c.3-.3.7-.4 1-.2 1.1.4 2.3.6 3.6.6.6 0 1 .4 1 1V20c0 .6-.4 1-1 1A17 17 0 0 1 3 4c0-.6.4-1 1-1h3.5c.6 0 1 .4 1 1 0 1.3.2 2.5.6 3.6.1.3 0 .7-.2 1z"/></svg>555 210 4400</li>
        <li><svg viewBox="0 0 24 24" aria-hidden="true"><path d="M7 1h10a2 2 0 0 1 2 2v18a2 2 0 0 1-2 2H7a2 2 0 0 1-2-2V3a2 2 0 0 1 2-2zm0 3v14h10V4zm5 15.5a1 1 0 1 0 0 2 1 1 0 0 0 0-2z"/></svg>555 210 4417</li>
        <li><svg viewBox="0 0 24 24" aria-hidden="true"><path d="M6 2h9l3 3v4h1a3 3 0 0 1 3 3v7h-4v3H6v-3H2v-7a3 3 0 0 1 3-3h1zm2 2v5h8V6h-2V4zm0 12v4h8v-4z"/></svg>555 210 4499</li>
        <li><svg viewBox="0 0 24 24" aria-hidden="true"><path d="M2 5h20v14H2zm2 2v.5l8 5 8-5V7z"/></svg>info@vantrellforge.com</li>
        <li><svg viewBox="0 0 24 24" aria-hidden="true"><path d="M12 2a10 10 0 1 0 0 20 10 10 0 0 0 0-20zm6.9 9h-3a15 15 0 0 0-1.3-6A8 8 0 0 1 18.9 11zM12 4c.9 1.2 1.8 3.6 1.9 7h-3.8C10.2 7.6 11.1 5.2 12 4zM9.4 5a15 15 0 0 0-1.3 6h-3A8 8 0 0 1 9.4 5zM5.1 13h3a15 15 0 0 0 1.3 6A8 8 0 0 1 5.1 13zm6.9 7c-.9-1.2-1.8-3.6-1.9-7h3.8c-.1 3.4-1 5.8-1.9 7zm2.6-1a15 15 0 0 0 1.3-6h3a8 8 0 0 1-4.3 6z"/></svg>www.vantrellforge.com</li>
      </ul>
    </div>
  </section>

</body>
</html>
```